Indy Film Production Company/Studio

We need a business card designed from an existing logo. We are a digital studio/production company that caters to creating genre entertainment, like Action, Horror, and martial arts. The card along with the logo will be used to Brand the company from letter heads to banners. The design will also be used for postcards and Brochures. It should be professional and masculine.
Updates

Thank you to all the designers who have participated. I'm narrowing down who it will be. Thank you again.

Target Market(s)

Investors, Networks, Producers, and actors

Industry/Entity Type

Film Production

Contact Information for Business Card

Teodoro Valbuena
Producer/Writer/Director
www.kestrelpicturehouse.example

Requirements
Must have
• Website address, Facebook icon and Twitter icon possibly in the back of the card.
Nice to have
• Logline of Company: Follow The Action.

```html
<!DOCTYPE html>
<html lang="en">
<head>
<meta charset="utf-8">
<title>Kestrel Picture House – Business Card</title>
<link rel="stylesheet" href="https://fonts.googleapis.com/css2?family=PT+Sans:wght@400;700&display=swap">
<style>
  :root {
    --backdrop: #4a403b;
    --card: #141414;
    --card-edge: #0a0a0a;
    --brand-red: #e8262d;
    --text-light: #f2f2f2;
    --rule: #6a6a6a;
  }
  * { margin: 0; padding: 0; box-sizing: border-box; }
  html, body {
    width: 1200px; height: 814px; overflow: hidden;
    background: var(--backdrop);
    font-family: "PT Sans", Arial, sans-serif;
  }
  .stage {
    position: relative; width: 1200px; height: 814px;
    display: flex; align-items: center; justify-content: center; gap: 50px;
  }
  .card {
    position: relative;
    width: 520px; height: 298px;
    background: var(--card);
    border: 1px solid var(--card-edge);
    box-shadow: 0 10px 24px rgba(0,0,0,.45);
    color: var(--text-light);
  }
  .wordmark {
    color: var(--brand-red);
    font-weight: 700;
    text-transform: uppercase;
    letter-spacing: 1px;
    line-height: 1;
  }
  /* Front side */
  .card-front .wordmark {
    position: absolute; right: 34px; top: 46px;
    font-size: 26px; text-align: right;
  }
  .card-front .divider {
    position: absolute; left: 30px; right: 30px; top: 126px;
    height: 1px; background: var(--rule);
  }
  .contact-block {
    position: absolute; left: 30px; top: 168px;
  }
  .person-name {
    color: var(--brand-red); font-size: 21px; font-weight: 400;
  }
  .person-role {
    font-size: 15px; margin-top: 2px;
  }
  .contact-rule {
    width: 150px; height: 1px; background: var(--rule); margin: 8px 0 6px;
  }
  .contact-list { list-style: none; }
  .contact-list li {
    display: flex; align-items: center; gap: 10px;
    font-size: 14px; line-height: 21px;
  }
  .contact-list svg { width: 13px; height: 13px; fill: var(--brand-red); flex: none; }
  /* Back side */
  .card-back .social-mark {
    position: absolute; right: 14px; top: 12px;
    width: 22px; height: 14px; background: var(--brand-red);
  }
  .card-back .wordmark {
    position: absolute; left: 0; right: 0; top: 104px;
    text-align: center; font-size: 34px;
  }
  .card-back .web {
    position: absolute; left: 0; right: 0; top: 186px;
    text-align: center; font-size: 14px; letter-spacing: .5px;
  }
</style>
</head>
<body>
<main class="stage">
  <section class="card card-front" aria-label="Business card front">
    <div class="wordmark">Kestrel<br>Picture House</div>
    <div class="divider"></div>
    <div class="contact-block">
      <p class="person-name">Teodoro Valbuena</p>
      <p class="person-role">Producer/Writer/Director</p>
      <div class="contact-rule"></div>
      <ul class="contact-list">
        <li>
          <svg viewBox="0 0 24 24" aria-hidden="true"><path d="M6.6 10.8a15.1 15.1 0 0 0 6.6 6.6l2.2-2.2a1 1 0 0 1 1-.25 11.4 11.4 0 0 0 3.6.6 1 1 0 0 1 1 1V20a1 1 0 0 1-1 1A17 17 0 0 1 3 4a1 1 0 0 1 1-1h3.5a1 1 0 0 1 1 1c0 1.25.2 2.45.6 3.6a1 1 0 0 1-.25 1z"/></svg>
          555 014 2290
        </li>
        <li>
          <svg viewBox="0 0 24 24" aria-hidden="true"><path d="M2 5h20v14H2z M3.5 6.5 12 13l8.5-6.5" stroke="#141414" stroke-width="1.6"/></svg>
          hello@kestrelpicturehouse.example
        </li>
        <li>
          <svg viewBox="0 0 24 24" aria-hidden="true"><circle cx="12" cy="12" r="10"/><path d="M2 12h20M12 2c3 3 3 17 0 20M12 2c-3 3-3 17 0 20" stroke="#141414" stroke-width="1.4" fill="none"/></svg>
          www.kestrelpicturehouse.example
        </li>
      </ul>
    </div>
  </section>

  <section class="card card-back" aria-label="Business card back">
    <span class="social-mark" aria-hidden="true"></span>
    <div class="wordmark">Kestrel Picture House</div>
    <p class="web">www.kestrelpicturehouse.example</p>
  </section>
</main>
</body>
</html>
```